Morlavik APP redesign and color change

I am looking for a new design for my app. Please see the attached current design.

Currently, I have a functioning app but the colors and design are awful!
The logo is great but the rest of the app needs a refresh.
(Logo hi res not yet available but will upload soon.)
New colors or anything that is cutting edge.

Basically: It is a secure social media app within a school system where the teachers, students and parents can text, exchange photos, plan curriculum, etc.

I NEED ONLY landing page with a new look!
Looking for one distinct design for the landing page with new look.
The developer will apply this one design towards the rest of the pages/app screens.

Because part of the social media I need the feel and look of what is now the trend. Something that will attract and keep the client(s) interested. I am really leaving all the creative work to the designer and open to any suggestions.

Target Market(s)

Schools, community, teachers, students, colleges, sport teams

Industry/Entity Type

Non Profit

Font styles to use
Serif
Sans Serif

Colors

Designer to choose colors to be used in the design.

Requirements
Must have
• Sharp, trendy, millennial feel
Nice to have
• Up to designer
Should not have
• Up to designer

```html
<!DOCTYPE html>
<html lang="en">
<head>
<meta charset="utf-8">
<title>Morlavik — App Screens</title>
<link href="https://fonts.googleapis.com/css2?family=Fira+Sans:wght@300;400;500&family=Fira+Sans+Condensed:wght@300;400;500&display=swap" rel="stylesheet">
<style>
  :root{
    --bg:#1f1f1f;
    --paper:#ffffff;
    --pink:#e8246f;
    --pink-2:#f0506a;
    --magenta:#e0197d;
    --ink:#333333;
    --muted:#9a9a9a;
    --line:#ececec;
    --teal:#2bb3c0;
    --grad:linear-gradient(90deg,var(--magenta),var(--pink-2));
  }
  *{box-sizing:border-box;margin:0;padding:0}
  html,body{width:1200px;height:800px;overflow:hidden;background:var(--bg)}
  body{font-family:"Fira Sans",sans-serif;color:var(--ink)}
  .gallery{position:relative;width:1200px;height:800px;display:flex;align-items:center;justify-content:center;gap:16px}
  .screen{position:relative;width:220px;height:391px;background:var(--paper);border-radius:4px;overflow:hidden;display:flex;flex-direction:column}

  .status-bar{height:16px;display:flex;align-items:center;justify-content:space-between;padding:0 6px;font-size:7px;color:#555;white-space:nowrap}
  .status-bar--light{color:#fff}
  .status-bar .battery{display:flex;align-items:center;gap:3px}
  .status-bar .battery i{display:inline-block;width:12px;height:5px;border:1px solid currentColor;border-radius:1px;position:relative}
  .status-bar .battery i::after{content:"";position:absolute;left:0;top:0;bottom:0;width:25%;background:currentColor}

  /* sign-up */
  .signup{padding:0 16px;font-family:"Fira Sans Condensed",sans-serif}
  .signup__heading{margin-top:44px;text-align:center;font-weight:300;font-size:12px;line-height:1.4;color:#666}
  .signup__fields{margin-top:18px;display:flex;flex-direction:column;gap:12px}
  .field{height:32px;background:var(--paper);border:1px solid var(--line);box-shadow:0 1px 4px rgba(0,0,0,.05);font-size:9px;font-weight:300;color:#bbb;display:flex;align-items:center;padding:0 8px}
  .terms{margin-top:16px;display:flex;align-items:center;gap:6px;font-size:7.5px;color:#555}
  .terms svg{width:8px;height:8px}
  .btn-primary{margin-top:16px;height:34px;background:var(--grad);color:#fff;font-size:11px;display:flex;align-items:center;justify-content:center;box-shadow:0 3px 8px rgba(232,36,111,.3)}
  .signup__footer{margin-top:12px;text-align:center;font-size:7px;color:#555}
  .signup__footer span{color:var(--teal)}

  /* landing */
  .landing{align-items:center;padding:0 14px}
  .landing__title{margin-top:52px;font-size:15px;font-weight:400;letter-spacing:8px;color:var(--pink);padding-left:8px}
  .landing__tagline{margin-top:4px;font-size:7.5px;font-weight:400;color:#333;letter-spacing:.2px}
  .landing__mark{margin-top:44px;display:flex;flex-direction:column;align-items:center;gap:10px}
  .landing__mark .dot{width:58px;height:58px;border-radius:50%;background:var(--pink)}
  .landing__mark .name{font-size:20px;font-weight:400;color:var(--pink)}
  .landing__prompt{margin-top:auto;font-size:9px;color:#333;letter-spacing:.3px}
  .landing__actions{margin:10px 0 24px;display:flex;gap:18px;width:100%}
  .landing__actions div{flex:1;height:30px;display:flex;align-items:center;justify-content:center;font-size:10px;letter-spacing:.4px}
  .btn-solid{background:var(--pink);color:#fff}
  .btn-outline{border:1.5px solid var(--pink);color:var(--pink)}

  /* conversations */
  .app-header{background:var(--grad);color:#fff}
  .app-header__bar{height:30px;display:flex;align-items:center;justify-content:space-between;padding:0 8px;font-size:8px}
  .app-header__brand{font-size:10px;font-weight:500}
  .app-header__icons{display:flex;gap:7px}
  .app-header__icons svg{width:10px;height:10px}
  .search{height:22px;display:flex;align-items:center;gap:5px;padding:0 8px;font-size:7px;color:var(--muted);border-bottom:1px solid var(--line)}
  .search svg{width:7px;height:7px}
  .threads{flex:1;display:flex;flex-direction:column}
  .thread{flex:1;display:flex;align-items:center;gap:7px;padding:0 8px;border-bottom:1px solid var(--line)}
  .avatar{width:22px;height:22px;border-radius:50%;background:linear-gradient(135deg,#c9a58d,#6b574b);flex:none}
  .thread__text{flex:1;display:flex;flex-direction:column;gap:2px}
  .thread__name{font-family:"Fira Sans Condensed",sans-serif;font-size:8.5px;color:#333}
  .thread__preview{font-family:"Fira Sans Condensed",sans-serif;font-size:6.5px;color:var(--muted)}
  .thread__action{width:16px;height:16px;border-radius:50%;background:var(--pink);display:flex;align-items:center;justify-content:center}
  .thread__action i{width:6px;height:6px;border-radius:50%;background:#fff}
  .tab-bar{height:30px;background:var(--grad);display:flex;align-items:center;justify-content:space-around}
  .tab-bar svg{width:11px;height:11px}

  /* chat */
  .chat-header__title{font-family:"Fira Sans Condensed",sans-serif;font-size:11px}
  .chat{flex:1;padding:8px;display:flex;flex-direction:column;gap:8px;font-family:"Fira Sans Condensed",sans-serif}
  .chat__time{text-align:center;font-size:6px;color:var(--pink)}
  .msg{display:flex;align-items:center;gap:4px;font-size:7px}
  .msg .avatar{width:12px;height:12px}
  .msg--in .bubble{background:var(--pink);color:#fff;padding:5px 7px}
  .msg--out{justify-content:flex-end}
  .msg--out .bubble{background:#fff;color:#555;padding:5px 7px;box-shadow:0 1px 3px rgba(0,0,0,.1)}
  .media{margin-left:14px;height:110px;background:#fff;box-shadow:0 1px 4px rgba(0,0,0,.12);padding:4px;display:flex;flex-direction:column;gap:6px}
  .media__frame{position:relative;flex:1;background:linear-gradient(135deg,#e6e2dc,#c9cdd3 60%,#b8bcc4)}
  .media__play{position:absolute;left:8px;top:50%;width:12px;height:12px;margin-top:-6px;border-radius:50%;background:var(--pink)}
  .media__progress{height:2px;background:#ddd;position:relative;margin:0 4px 4px}
  .media__progress::before{content:"";position:absolute;left:0;top:0;bottom:0;width:35%;background:var(--pink)}
  .media__progress::after{content:"";position:absolute;left:35%;top:-2px;width:6px;height:6px;margin-left:-3px;border-radius:50%;background:var(--pink)}
  .composer{height:32px;border-top:1px solid var(--line);display:flex;align-items:center;gap:5px;padding:0 8px;font-family:"Fira Sans Condensed",sans-serif;font-size:7px;color:#777}
  .composer span{flex:1}
  .composer i{width:14px;height:14px;border-radius:50%;background:var(--pink)}
</style>
</head>
<body>
<main class="gallery">

  <section class="screen signup">
    <div class="status-bar"><span>●●●○○ VELOQ</span><span>4:21 PM</span><span class="battery">22% <i></i></span></div>
    <p class="signup__heading">You are New Here<br>Please Sign Up</p>
    <div class="signup__fields">
      <div class="field">Username</div>
      <div class="field">Password</div>
      <div class="field">Confirm Password</div>
    </div>
    <div class="terms"><svg viewBox="0 0 10 10"><path d="M1 5l3 3 5-6" fill="none" stroke="#333" stroke-width="1.5"/></svg>Accept Terms &amp; Conditions</div>
    <div class="btn-primary">Sign Up Now</div>
    <p class="signup__footer">Already have an account? <span>Sign up</span></p>
  </section>

  <section class="screen signup">
    <div class="status-bar"><span>●●●○○ VELOQ</span><span>4:21 PM</span><span class="battery">22% <i></i></span></div>
    <p class="signup__heading">You are New Here<br>Please Sign Up</p>
    <div class="signup__fields">
      <div class="field">Username</div>
      <div class="field">Password</div>
      <div class="field">Confirm Password</div>
    </div>
    <div class="terms"><svg viewBox="0 0 10 10"><path d="M1 5l3 3 5-6" fill="none" stroke="#333" stroke-width="1.5"/></svg>Accept Terms &amp; Conditions</div>
    <div class="btn-primary">Sign Up Now</div>
    <p class="signup__footer">Already have an account? <span>Sign up</span></p>
  </section>

  <section class="screen landing">
    <div class="status-bar" style="width:calc(100% + 28px)"><span>●●●○○ VELOQ</span><span>4:21 PM</span><span class="battery">22% <i></i></span></div>
    <h1 class="landing__title">MORLAVIK</h1>
    <p class="landing__tagline">SECURITY THROUGH TRANSPARENCY</p>
    <div class="landing__mark"><span class="dot"></span><span class="name">Morlavik</span></div>
    <p class="landing__prompt">Create a new account or sign in</p>
    <div class="landing__actions">
      <div class="btn-solid">Get Started</div>
      <div class="btn-outline">Sign In</div>
    </div>
  </section>

  <section class="screen conversations">
    <header class="app-header">
      <div class="status-bar status-bar--light"><span>●●●○○ VELOQ</span><span>4:21 PM</span><span class="battery">22% <i></i></span></div>
      <div class="app-header__bar">
        <span>‹ Back</span>
        <span class="app-header__brand">Morlavik</span>
        <span class="app-header__icons">
          <svg viewBox="0 0 10 10"><circle cx="5" cy="5" r="4" fill="none" stroke="#fff" stroke-width="1.2"/><path d="M1 5h8M5 1c2 2 2 6 0 8M5 1c-2 2-2 6 0 8" fill="none" stroke="#fff" stroke-width=".8"/></svg>
          <svg viewBox="0 0 10 10"><circle cx="4" cy="4" r="3" fill="none" stroke="#fff" stroke-width="1.3"/><path d="M6.3 6.3L9 9" stroke="#fff" stroke-width="1.4"/></svg>
        </span>
      </div>
    </header>
    <div class="search"><svg viewBox="0 0 10 10"><circle cx="4" cy="4" r="3" fill="none" stroke="#e8246f" stroke-width="1.3"/><path d="M6.3 6.3L9 9" stroke="#e8246f" stroke-width="1.4"/></svg>Search Conversations...</div>
    <div class="threads">
      <div class="thread"><span class="avatar" role="img" aria-label="Contact photo"></span><div class="thread__text"><span class="thread__name">Selma Varga</span><span class="thread__preview">Hlo How Are You ?</span></div><span class="thread__action"><i></i></span></div>
      <div class="thread"><span class="avatar" role="img" aria-label="Contact photo"></span><div class="thread__text"><span class="thread__name">Tobias Reyne</span><span class="thread__preview">Tonight I am Going Home</span></div><span class="thread__action"><i></i></span></div>
      <div class="thread"><span class="avatar" role="img" aria-label="Contact photo"></span><div class="thread__text"><span class="thread__name">Marco Ellis</span><span class="thread__preview">So Whats Going on There</span></div><span class="thread__action"><i></i></span></div>
      <div class="thread"><span class="avatar" role="img" aria-label="Contact photo"></span><div class="thread__text"><span class="thread__name">Ines Holt</span><span class="thread__preview">Hlo All Things is Working</span></div><span class="thread__action"><i></i></span></div>
      <div class="thread"><span class="avatar" role="img" aria-label="Contact photo"></span><div class="thread__text"><span class="thread__name">Dario Quist</span><span class="thread__preview">Amazing App Design</span></div><span class="thread__action"><i></i></span></div>
      <div class="thread"><span class="avatar" role="img" aria-label="Contact photo"></span><div class="thread__text"><span class="thread__name">Clara Wend</span><span class="thread__preview">This Gona Be Rock</span></div><span class="thread__action"><i></i></span></div>
    </div>
    <nav class="tab-bar">
      <svg viewBox="0 0 12 12"><rect x="1" y="2" width="10" height="7" fill="none" stroke="#fff" stroke-width="1"/><path d="M3 9v2l2-2" fill="none" stroke="#fff"/></svg>
      <svg viewBox="0 0 12 12"><rect x="1" y="1" width="4" height="4" fill="none" stroke="#fff"/><rect x="7" y="1" width="4" height="4" fill="none" stroke="#fff"/><rect x="1" y="7" width="4" height="4" fill="none" stroke="#fff"/><rect x="7" y="7" width="4" height="4" fill="none" stroke="#fff"/></svg>
      <svg viewBox="0 0 12 12"><rect x="2" y="1" width="8" height="10" fill="none" stroke="#fff"/><circle cx="6" cy="6" r="2" fill="none" stroke="#fff"/></svg>
      <svg viewBox="0 0 12 12"><circle cx="6" cy="6" r="2" fill="none" stroke="#fff"/><circle cx="6" cy="6" r="4.5" fill="none" stroke="#fff" stroke-dasharray="2 1.5"/></svg>
    </nav>
  </section>

  <section class="screen chat-screen">
    <header class="app-header">
      <div class="status-bar status-bar--light"><span>●●●○○ VELOQ</span><span>4:21 PM</span><span class="battery">22% <i></i></span></div>
      <div class="app-header__bar"><span class="chat-header__title">‹ Selma Varga</span></div>
    </header>
    <div class="chat">
      <p class="chat__time">9:20 PM</p>
      <div class="msg msg--in"><span class="avatar" role="img" aria-label="Sender photo"></span><span class="bubble">Hlo How Are You ?</span></div>
      <div class="msg msg--out"><span class="bubble">I'm Fine You Say Dear</span><span class="avatar" role="img" aria-label="Your photo"></span></div>
      <div class="msg msg--in"><span class="avatar" role="img" aria-label="Sender photo"></span><span class="bubble">Please send me video :D</span></div>
      <div class="media">
        <div class="media__frame" role="img" aria-label="Shared video thumbnail of a fashion portrait"><span class="media__play"></span></div>
        <div class="media__progress"></div>
      </div>
    </div>
    <div class="composer"><span>Type here...</span><i></i><i></i><i></i></div>
  </section>

</main>
</body>
</html>
```